Advertising company unique advertising platform

we need a logo design for a new company based in Australia Melbourne. We develop innovated advertising platform where consumer can use this platform to get regular discount, as business owner they can use this platform for free advertisement. Payment for this advertisement platform only payable every two weeks, when I generate revenue for their business

Industry/Entity Type

Advertising

Contact Information for Business Card

Dale Morven | Co-Founder |Managing Director
Suite 718 240 Wattlebrook Lane Melbourne Vic 3000

ABN 38 614 207 923
Tel: +61 0487 259 318 | Email: dale.morven@plivorantu.com

Font styles to use
Decorative
Script

Requirements
Must have
• Try few different design and some round corner business card
Should not have
• One round corner business card...try 4 different colour background not only black, make sure two side is designed. Be creative so imagine you are giving this to a client make sure has wow factor, if you can also try one design with engrave like all the logo, words look 3d feel
• The word Advertising Platform use attached file font

```html
<!DOCTYPE html>
<html lang="en">
<head>
<meta charset="utf-8">
<title>Plivo Rantu – Business Card</title>
<link rel="stylesheet" href="https://fonts.googleapis.com/css2?family=Open+Sans:wght@400;700&display=swap">
<style>
  :root {
    --canvas: #e9e6e2;
    --card-dark: #2a2a2a;
    --teal: #12e8ae;
    --sky: #12b8f2;
    --lilac: #8fa6e0;
    --flame: #e8482a;
    --amber: #f5a03a;
    --gold: #f3c54a;
    --ink: #222222;
    --white: #ffffff;
    --shadow: rgba(0,0,0,0.35);
  }
  * { margin: 0; padding: 0; box-sizing: border-box; }
  html, body { width: 1200px; height: 960px; overflow: hidden; }
  body {
    background: var(--canvas);
    font-family: "Open Sans", Arial, sans-serif;
    position: relative;
  }
  .card {
    position: absolute;
    width: 600px;
    height: 343px;
    border-radius: 22px;
    overflow: hidden;
    box-shadow: 2px 4px 8px var(--shadow);
  }
  .card-front { left: 315px; top: 113px; background: var(--card-dark); }
  .card-back {
    left: 312px; top: 473px; height: 342px;
    background: radial-gradient(ellipse 60% 75% at 50% 40%, var(--gold) 0%, var(--amber) 45%, var(--flame) 100%);
  }
  .front-art { position: absolute; inset: 0; }

  .brand {
    position: absolute;
    display: flex;
    align-items: center;
    gap: 10px;
    font-weight: 700;
    white-space: nowrap;
  }
  .brand-front { left: 40px; top: 170px; color: var(--flame); font-size: 26px; }
  .brand-front .brand-dot { width: 30px; height: 30px; border-radius: 50%; background: var(--flame); }
  .brand-back { left: 0; right: 0; top: 130px; justify-content: center; color: var(--white); font-size: 40px; }
  .brand-back .brand-dot { width: 44px; height: 44px; border-radius: 50%; background: var(--white); }

  .contact {
    position: absolute;
    right: 26px;
    top: 56px;
    text-align: right;
    color: var(--ink);
    font-size: 14.5px;
    line-height: 20px;
  }
  .contact .name { font-weight: 700; font-size: 16px; line-height: 22px; }
  .contact .role { font-size: 16px; line-height: 22px; }
  .contact .company { margin-top: 12px; }
  .contact .address { margin-top: 2px; }
  .contact .reach { margin-top: 4px; }
  .contact .reach-line { display: flex; justify-content: flex-end; align-items: center; gap: 6px; }
  .contact .icon { width: 14px; height: 12px; fill: var(--ink); }

  .website {
    position: absolute;
    left: 0; right: 0; top: 292px;
    text-align: center;
    color: var(--white);
    font-size: 13px;
    letter-spacing: 4px;
  }
</style>
</head>
<body>

<section class="card card-front">
  <svg class="front-art" viewBox="0 0 600 343" width="600" height="343" aria-hidden="true">
    <defs>
      <linearGradient id="panelGradient" x1="0" y1="0" x2="1" y2="0.4">
        <stop offset="0" stop-color="var(--teal)"/>
        <stop offset="0.6" stop-color="var(--lilac)"/>
        <stop offset="1" stop-color="var(--sky)"/>
      </linearGradient>
      <linearGradient id="swooshGradient" x1="0" y1="0" x2="0" y2="1">
        <stop offset="0" stop-color="var(--amber)"/>
        <stop offset="1" stop-color="var(--flame)"/>
      </linearGradient>
    </defs>
    <path d="M238,0 C300,30 330,130 326,210 C322,290 270,330 220,343 L250,343 C300,320 336,270 338,205 C340,130 305,40 248,0 Z" fill="url(#swooshGradient)"/>
    <path d="M248,0 C305,40 340,130 338,205 C336,270 300,320 250,343 L600,343 L600,0 Z" fill="url(#panelGradient)"/>
  </svg>

  <div class="brand brand-front">
    <span class="brand-dot"></span>
    <span class="brand-name">Brightlane Hub</span>
  </div>

  <div class="contact">
    <div class="name">DALE MORVEN</div>
    <div class="role">CO-FOUNDER</div>
    <div class="role">MANAGING DIRECTOR</div>
    <div class="company">Plivo Rantu</div>
    <div>ABN 38 614 207 923</div>
    <div class="address">Suite 718 240</div>
    <div>Wattlebrook Lane</div>
    <div>Melbourne Vic 3000</div>
    <div class="reach">
      <div class="reach-line">+61 0487 259 318
        <svg class="icon" viewBox="0 0 14 12" aria-hidden="true"><path d="M1,4 C1,1 13,1 13,4 L10,5 L9,3 L5,3 L4,5 Z M3,6 L11,6 L12,11 L2,11 Z"/></svg>
      </div>
      <div class="reach-line">dale.morven@plivorantu.com
        <svg class="icon" viewBox="0 0 14 12" aria-hidden="true"><path d="M1,2 L13,2 L7,7 Z M1,4 L7,9 L13,4 L13,10 L1,10 Z"/></svg>
      </div>
    </div>
  </div>
</section>

<section class="card card-back">
  <div class="brand brand-back">
    <span class="brand-dot"></span>
    <span class="brand-name">Brightlane Hub</span>
  </div>
  <div class="website">www.plivorantu.com</div>
</section>

</body>
</html>
```